Business Card Design for company

We want new business cards. We'd like something different-- yet still highly professional. Our tagline is Providing leadership, delivering success. Stock photos are ok, as long as they are relevant and look upscale.

Target Market(s)

Architecture/Business Management Consulting/Engineering Consulting

Contact Information for Business Card

dark gray background with pops of blue might be good, but you tell me. You're the designers. Rounded corners might be nice, but again, you tell me.

Font styles to use
Serif
Sans Serif

Colors
3276b5
5c5c5c
9d9d9d
fbfbfb

Requirements
Nice to have
• Something different, but still very professional.

```html
<!DOCTYPE html>
<html lang="en">
<head>
<meta charset="utf-8">
<title>Norvale International – Business Card</title>
<link href="https://fonts.googleapis.com/css2?family=Carlito:wght@400;700&display=swap" rel="stylesheet">
<style>
  :root {
    --blue: #3276b5;
    --blue-light: #6bb4d6;
    --blue-name: #4a9acb;
    --grey-dark: #5c5c5c;
    --grey-mid: #9d9d9d;
    --paper: #ffffff;
    --backdrop: #fbfbfb;
    --ink: #222222;
  }
  html, body {
    margin: 0;
    width: 1200px;
    height: 1023px;
    overflow: hidden;
    background: var(--backdrop);
    font-family: "Carlito", "Open Sans", sans-serif;
  }
  .canvas {
    position: relative;
    width: 1200px;
    height: 1023px;
  }
  .card {
    position: absolute;
    left: 150px;
    top: 254px;
    width: 900px;
    height: 514px;
    background: var(--paper);
    box-shadow: 0 2px 10px rgba(0,0,0,0.12);
    overflow: hidden;
  }
  .card__band {
    position: absolute;
    right: 0;
    top: 0;
    width: 112px;
    height: 100%;
    background: linear-gradient(180deg, var(--blue) 0%, #3a86bf 60%, var(--blue-light) 100%);
  }
  .brand {
    position: absolute;
    left: 62px;
    top: 212px;
    width: 330px;
    display: flex;
    align-items: center;
    gap: 14px;
  }
  .brand__mark {
    width: 26px;
    height: 26px;
    background: var(--blue);
    flex: none;
  }
  .brand__name {
    font-weight: 400;
    font-size: 38px;
    letter-spacing: 1px;
    color: var(--blue);
    line-height: 1.1;
  }
  .card__divider {
    position: absolute;
    left: 418px;
    top: 140px;
  }
  .contact {
    position: absolute;
    left: 468px;
    top: 96px;
  }
  .contact__name {
    margin: 0;
    font-size: 32px;
    font-weight: 400;
    color: var(--blue-name);
    line-height: 1;
  }
  .contact__role {
    margin: 2px 0 0;
    font-size: 22px;
    color: var(--grey-dark);
  }
  .contact__list {
    list-style: none;
    margin: 34px 0 0 0;
    padding: 0;
    font-size: 21px;
    color: var(--ink);
    line-height: 1.22;
  }
  .contact__item {
    display: flex;
    align-items: flex-start;
    gap: 12px;
    margin-bottom: 3px;
  }
  .contact__icon {
    width: 18px;
    height: 18px;
    margin-top: 4px;
    flex: none;
  }
</style>
</head>
<body>
<main class="canvas">
  <section class="card">
    <div class="brand">
      <span class="brand__mark"></span>
      <span class="brand__name">Norvale International</span>
    </div>

    <svg class="card__divider" width="6" height="240" viewBox="0 0 6 240" aria-hidden="true">
      <polygon points="2,0 4,0 5,240 1,240" fill="var(--blue)"/>
    </svg>

    <div class="contact">
      <h1 class="contact__name">Daniel Hart</h1>
      <p class="contact__role">Owner</p>
      <ul class="contact__list">
        <li class="contact__item">
          <svg class="contact__icon" viewBox="0 0 18 18" aria-hidden="true">
            <rect width="18" height="18" rx="3" fill="var(--blue)"/>
            <path d="M5 4 L7.5 4 L8.3 6.8 L7 8 Q8 10.2 10 11 L11.2 9.7 L14 10.5 L14 13 Q8 14 5 7 Z" fill="#fff"/>
          </svg>
          <span>+0000-0000-0000</span>
        </li>
        <li class="contact__item">
          <svg class="contact__icon" viewBox="0 0 18 18" aria-hidden="true">
            <rect width="18" height="18" rx="3" fill="var(--blue)"/>
            <rect x="4" y="5.5" width="10" height="7" fill="none" stroke="#fff" stroke-width="1.4"/>
            <polyline points="4,5.5 9,9.5 14,5.5" fill="none" stroke="#fff" stroke-width="1.4"/>
          </svg>
          <span>info@yourdomain.com</span>
        </li>
        <li class="contact__item">
          <svg class="contact__icon" viewBox="0 0 18 18" aria-hidden="true">
            <rect width="18" height="18" rx="3" fill="var(--blue)"/>
            <circle cx="9" cy="9" r="5" fill="none" stroke="#fff" stroke-width="1.3"/>
            <ellipse cx="9" cy="9" rx="2" ry="5" fill="none" stroke="#fff" stroke-width="1.1"/>
            <line x1="4" y1="9" x2="14" y2="9" stroke="#fff" stroke-width="1.1"/>
          </svg>
          <span>www.yourdomain.com</span>
        </li>
        <li class="contact__item">
          <svg class="contact__icon" viewBox="0 0 18 18" aria-hidden="true">
            <rect width="18" height="18" rx="3" fill="var(--blue)"/>
            <path d="M9 15 Q4.5 9.5 4.5 7.5 A4.5 4.5 0 0 1 13.5 7.5 Q13.5 9.5 9 15 Z" fill="#fff"/>
            <circle cx="9" cy="7.5" r="1.7" fill="var(--blue)"/>
          </svg>
          <span>Studio 21,<br>8 Marlow Street,<br>London</span>
        </li>
      </ul>
    </div>

    <div class="card__band"></div>
  </section>
</main>
</body>
</html>
```